Dusty Spur Outfitters Home Page

I need a logo and page design for my home page, maybe some background color suggestions to go with it. I want the logo to project "vintage" and "western wear" but not be your typical trite western saddle and gun type thing.
http://www.dustyspuroutfitters.example/store/cart.php
Not looking for page coding just logo and other design elements to lay in over the site's template to make it "pop"
Reason: Have to finalize the design.
Target Market(s)
My customers are 70/30 men to women.
Industry/Entity Type
Gun

```html
<!DOCTYPE html>
<html lang="en">
<head>
<meta charset="utf-8">
<title>Dusty Spur Outfitters – Header Options</title>
<link href="https://fonts.googleapis.com/css2?family=Lato:wght@700;900&family=Yesteryear&display=swap" rel="stylesheet">
<style>
  :root {
    --canvas-beige: #cdbc9c;
    --band-teal: #4a929c;
    --band-dark-leather: #1f1e1e;
    --band-dark-grunge: #242222;
    --band-dark-canvas: #1b1917;
    --cream: #eadfc4;
    --tagline-cream: #d9d0bb;
    --search-fill: #e6dcc6;
    --search-text: #3a3530;
  }
  * { margin: 0; padding: 0; box-sizing: border-box; }
  html, body {
    width: 1200px;
    height: 1000px;
    overflow: hidden;
    background: var(--canvas-beige);
  }
  .header-options {
    position: relative;
    width: 1200px;
    height: 1000px;
  }
  .site-header {
    position: absolute;
    left: 0;
    width: 1200px;
    height: 165px;
    background: var(--band-teal);
    box-shadow: 0 3px 4px rgba(0, 0, 0, 0.35);
  }
  .site-header--leather { top: 147px; }
  .site-header--grunge  { top: 417px; }
  .site-header--canvas  { top: 687px; }

  .header-body {
    position: absolute;
    left: 0;
    top: 16px;
    width: 100%;
    height: 133px;
  }
  .site-header--leather .header-body { background: var(--band-dark-leather); }
  .site-header--grunge  .header-body { background: var(--band-dark-grunge); }
  .site-header--canvas  .header-body { background: var(--band-dark-canvas); }

  .brand-name {
    position: absolute;
    left: 62px;
    top: 62px;
    font-family: "Lato", sans-serif;
    font-weight: 900;
    font-size: 32px;
    letter-spacing: 0.5px;
    color: var(--cream);
    white-space: nowrap;
  }
  .tagline {
    position: absolute;
    left: 476px;
    top: 86px;
    font-family: "Yesteryear", cursive;
    font-size: 25px;
    color: var(--tagline-cream);
    white-space: nowrap;
  }
  .search {
    position: absolute;
    left: 901px;
    top: 51px;
    display: flex;
    align-items: center;
  }
  .search-field {
    width: 173px;
    height: 30px;
    border-radius: 15px;
    background: var(--search-fill);
    font-family: "Lato", sans-serif;
    font-weight: 700;
    font-size: 17px;
    line-height: 30px;
    color: var(--search-text);
    padding-left: 17px;
  }
  .search-go {
    margin-left: 10px;
    font-family: "Lato", sans-serif;
    font-weight: 700;
    font-size: 18px;
    color: var(--search-fill);
  }
</style>
</head>
<body>
<main class="header-options">

  <header class="site-header site-header--leather">
    <div class="header-body" role="img" aria-label="Black leather texture band">
      <div class="brand-name">Dusty Spur Outfitters</div>
      <div class="tagline">Brand-New Retro Styled Western Wear</div>
      <div class="search">
        <div class="search-field">Search...</div>
        <div class="search-go">GO!</div>
      </div>
    </div>
  </header>

  <header class="site-header site-header--grunge">
    <div class="header-body" role="img" aria-label="Distressed dark grunge texture band">
      <div class="brand-name">Dusty Spur Outfitters</div>
      <div class="tagline">Brand-New Retro Styled Western Wear</div>
      <div class="search">
        <div class="search-field">Search...</div>
        <div class="search-go">GO!</div>
      </div>
    </div>
  </header>

  <header class="site-header site-header--canvas">
    <div class="header-body" role="img" aria-label="Dark worn canvas texture band">
      <div class="brand-name">Dusty Spur Outfitters</div>
      <div class="tagline">Brand-New Retro Styled Western Wear</div>
      <div class="search">
        <div class="search-field">Search...</div>
        <div class="search-go">GO!</div>
      </div>
    </div>
  </header>

</main>
</body>
</html>
```